1 Page for Computer Repair Website

Looking for a 1 page website with a design that compliments the business card and pamphlet that have already been made (attached files). It should look business professional and easy to read. Email and phone number should be somewhere near the top of the website, visible when the page loads. I don't want any forms for people to mess with. No "Contact Us" form or entering in email for newsletter. Customers will just be looking at this site to confirm we are professionals and have our business in order.

Target Market(s)

Home and small business

Industry/Entity Type

Computer Repair

Coding

Coded - Design and coding required

Number of Pages Required

1 page

Font styles to use
Other font styles liked:
• Helvetica variations used in pamphlet and card

Colors
0455a3
cfdeed
85abd2
3276b5
85cae6
ffffff

Requirements
Must have
• Compliment the pamphlet and business card in color choices and font use. Pleasing to the eye and easy to read through categories and text.
Should not have
• Forms. No "enter name and email here" or anything of the sort.

```html
<!DOCTYPE html>
<html lang="en">
<head>
<meta charset="utf-8">
<title>Techmend – Computer Service &amp; Repair</title>
<link rel="stylesheet" href="https://fonts.googleapis.com/css2?family=Roboto:wght@300;400;500;700&display=swap">
<style>
:root{
  --brand:#0455a3;
  --brand-mid:#3276b5;
  --brand-soft:#85abd2;
  --sky:#85cae6;
  --ice:#cfdeed;
  --white:#ffffff;
  --navy:#0b2a52;
  --hero-deep:#071c3a;
  --ink:#333b45;
  --muted:#8a9099;
  --rule:#e3e6ea;
  --band:#ececec;
  --footer:#2b2b2b;
  --footer-deep:#1f1f1f;
}
*{margin:0;padding:0;box-sizing:border-box}
html,body{width:1200px;height:2436px;overflow:hidden}
body{font-family:"Roboto",Helvetica,Arial,sans-serif;color:var(--ink);background:var(--white);font-size:14px;line-height:1.6}
.wrap{width:1040px;margin:0 auto;position:relative}

/* header */
.site-header{height:96px;background:var(--white);border-bottom:1px solid var(--rule)}
.site-header .wrap{height:96px}
.brand{position:absolute;left:0;top:18px}
.brand-name{font-size:44px;font-weight:700;color:var(--navy);line-height:1;letter-spacing:-1px}
.brand-tag{font-size:13px;color:var(--brand-mid);letter-spacing:1px;margin-top:2px}
.contact-bar{position:absolute;right:0;top:14px;font-size:13px;color:var(--ink);display:flex;gap:26px}
.contact-bar span{display:flex;align-items:center;gap:6px}
.contact-bar b{color:var(--brand);font-weight:500}
.main-nav{position:absolute;right:0;top:58px;display:flex;gap:52px;font-size:13px}
.main-nav a{color:var(--ink);text-decoration:none}
.main-nav a.active{color:var(--brand)}

/* hero */
.hero{height:504px;background:radial-gradient(circle at 78% 45%,#1a4f8c 0%,#0c2f5e 35%,var(--hero-deep) 80%);position:relative;overflow:hidden}
.hero-art{position:absolute;right:90px;top:70px;width:360px;height:360px;border-radius:50%;background:radial-gradient(circle,#2fa6de 0%,#0e5fa6 45%,rgba(7,28,58,0) 72%)}
.hero-copy{position:absolute;left:80px;top:96px;width:440px}
.hero-title{font-size:60px;font-weight:400;color:var(--white);line-height:1}
.hero-sub{font-size:32px;font-weight:300;color:var(--sky);margin-top:8px;line-height:1.2}
.hero-text{font-size:14px;color:var(--ice);margin-top:22px;line-height:1.7}
.btn{display:inline-block;background:var(--brand);color:var(--white);font-size:12px;font-weight:500;padding:10px 24px;text-decoration:none;letter-spacing:.5px}
.btn-hero{background:var(--brand-mid);margin-top:26px}

/* section heads */
.section-title{text-align:center;font-size:26px;font-weight:500;color:var(--ink);letter-spacing:1px}
.section-rule{width:60px;height:2px;background:var(--brand);margin:14px auto 0}
.section-intro{text-align:center;font-size:13px;color:var(--muted);width:820px;margin:18px auto 0}

/* welcome */
.welcome{height:640px;padding-top:72px;border-bottom:1px solid var(--rule)}
.cards{display:flex;gap:58px;margin-top:44px}
.card{width:308px}
.card-media{height:184px;width:100%}
.media-office{background:linear-gradient(135deg,#f2f4f6,#c9ced6)}
.media-hands{background:linear-gradient(135deg,#3a4a5c,#1c6b8e)}
.media-solution{background:linear-gradient(135deg,#0a2a5c,#1f6db3)}
.card h3{font-size:18px;font-weight:700;color:var(--ink);margin-top:22px}
.card p{font-size:13px;color:var(--muted);margin-top:8px;line-height:1.65}
.card .btn{margin-top:18px}

/* services */
.services{height:580px;padding-top:64px}
.service-grid{display:grid;grid-template-columns:1fr 1fr;column-gap:70px;row-gap:40px;margin-top:48px}
.service{display:flex;gap:22px}
.service-icon{flex:0 0 54px;height:54px;border-radius:50%;background:var(--navy);display:flex;align-items:center;justify-content:center}
.service h4{font-size:15px;font-weight:700;color:var(--ink)}
.service p{font-size:13px;color:var(--muted);margin-top:6px;line-height:1.65}
.dots{display:flex;justify-content:center;gap:8px;margin-top:46px}
.dots i{width:8px;height:8px;border-radius:50%;background:#c6c9ce}
.dots i.on{background:var(--brand)}

/* testimonials */
.testimonials{height:280px;background:var(--band);padding-top:44px}
.quotes{display:flex;gap:80px;margin:38px 0 0 60px}
.quote{display:flex;gap:22px;width:420px}
.avatar{flex:0 0 100px;height:100px;border-radius:50%;background:linear-gradient(160deg,#d7c2b2,#8c7a6e)}
.quote p{font-size:13px;color:var(--muted);line-height:1.65}
.quote .who{font-size:12px;font-weight:700;color:var(--ink);margin-top:10px}
.quote .role{font-size:11px;color:var(--muted)}

/* footer */
.site-footer{height:300px;background:var(--footer);color:#b9bcc1;padding-top:44px}
.footer-cols{display:flex}
.footer-brand{width:300px}
.footer-brand .brand-name{color:var(--white);font-size:40px}
.footer-brand .brand-tag{color:var(--sky)}
.footer-col{width:185px}
.footer-col h5{font-size:14px;font-weight:500;color:var(--white);letter-spacing:1px;margin-bottom:14px}
.footer-col li{list-style:none;font-size:12px;line-height:2.1}
.social li{display:flex;align-items:center;gap:10px}
.social-dot{width:22px;height:22px;border-radius:50%;border:1px solid #8a8e94}
.footer-bottom{height:36px;background:var(--footer-deep);color:#8a8e94;font-size:11px;display:flex;align-items:center;justify-content:center}
</style>
</head>
<body>

<header class="site-header">
  <div class="wrap">
    <div class="brand">
      <div class="brand-name">Techmend</div>
      <div class="brand-tag">Computer Services</div>
    </div>
    <div class="contact-bar">
      <span>
        <svg width="14" height="14" viewBox="0 0 24 24"><path fill="#0455a3" d="M6.6 10.8a15 15 0 0 0 6.6 6.6l2.2-2.2c.3-.3.7-.4 1-.2 1.1.4 2.3.6 3.6.6.6 0 1 .4 1 1V20c0 .6-.4 1-1 1A17 17 0 0 1 3 4c0-.6.4-1 1-1h3.5c.6 0 1 .4 1 1 0 1.3.2 2.5.6 3.6.1.3 0 .7-.2 1z"/></svg>
        Call Us: <b>1 (555) 014 2290</b>
      </span>
      <span>
        <svg width="15" height="12" viewBox="0 0 24 18"><rect x="1" y="1" width="22" height="16" fill="none" stroke="#0455a3" stroke-width="2"/><path d="M1 1l11 9 11-9" fill="none" stroke="#0455a3" stroke-width="2"/></svg>
        Email: <b>hello@techmend.example</b>
      </span>
    </div>
    <nav class="main-nav">
      <a class="active" href="#home">Home</a>
      <a href="#about">About Us</a>
      <a href="#services">Services</a>
      <a href="#testimonials">Testimonials</a>
      <a href="#contact">Contact Us</a>
    </nav>
  </div>
</header>

<section class="hero" id="home">
  <div class="hero-art" role="img" aria-label="Glowing blue power button on a dark circuit-board background"></div>
  <div class="hero-copy">
    <h1 class="hero-title">WE ARE A</h1>
    <p class="hero-sub">computer service &amp; repair company</p>
    <p class="hero-text">We repair desktops, laptops and home networks quickly and honestly, with clear prices up front and friendly advice for every household and small office since 1999.</p>
    <a class="btn btn-hero" href="#about">READ MORE</a>
  </div>
</section>

<section class="welcome" id="about">
  <div class="wrap">
    <h2 class="section-title">WELCOME TO TECHMEND</h2>
    <div class="section-rule"></div>
    <p class="section-intro">Our certified technicians keep home users and small businesses running. We diagnose problems fast, explain every repair in plain words and stand behind the work we do, so you can get back to what matters most.</p>
    <div class="cards">
      <article class="card">
        <div class="card-media media-office" role="img" aria-label="Bright office workspace with computers"></div>
        <h3>Who we are?</h3>
        <p>A local team of repair specialists with years of hands-on experience fixing computers for families, freelancers and growing offices across the area.</p>
        <a class="btn" href="#about">Read More</a>
      </article>
      <article class="card">
        <div class="card-media media-hands" role="img" aria-label="Technician working on a computer circuit board"></div>
        <h3>What we do?</h3>
        <p>Hardware repair, virus removal, upgrades, data recovery and network setup, all handled with care, tested twice and returned ready to use.</p>
        <a class="btn" href="#services">Read More</a>
      </article>
      <article class="card">
        <div class="card-media media-solution" role="img" aria-label="Blue illustration of a puzzle piece labelled solution"></div>
        <h3>Why choose us?</h3>
        <p>Honest quotes, quick turnaround and no hidden fees. We treat every machine as if it were our own and keep you informed at every step.</p>
        <a class="btn" href="#testimonials">Read More</a>
      </article>
    </div>
  </div>
</section>

<section class="services" id="services">
  <div class="wrap">
    <h2 class="section-title">OUR SERVICES</h2>
    <div class="section-rule"></div>
    <p class="section-intro">From a slow laptop to a full office network, we offer practical services at fair prices, delivered by people who enjoy solving computer problems.</p>
    <div class="service-grid">
      <div class="service">
        <div class="service-icon"><svg width="24" height="24" viewBox="0 0 24 24"><path d="M4 12l5 5 11-11" fill="none" stroke="#fff" stroke-width="2.5"/></svg></div>
        <div><h4>HONEST SERVICE</h4><p>We tell you exactly what is wrong and what it will cost before any work begins. If a repair is not worth it, we will say so and suggest better options.</p></div>
      </div>
      <div class="service">
        <div class="service-icon"><svg width="24" height="24" viewBox="0 0 24 24"><path d="M12 2l8 3v6c0 5-3.5 9-8 11-4.5-2-8-6-8-11V5z" fill="none" stroke="#fff" stroke-width="2"/></svg></div>
        <div><h4>MALWARE/VIRUS REMOVAL</h4><p>We clean infected systems thoroughly, restore lost settings and install solid protection so the same trouble does not come back next month.</p></div>
      </div>
      <div class="service">
        <div class="service-icon"><svg width="24" height="24" viewBox="0 0 24 24"><rect x="4" y="5" width="16" height="11" fill="none" stroke="#fff" stroke-width="2"/><path d="M2 19h20" stroke="#fff" stroke-width="2"/></svg></div>
        <div><h4>PC/MAC/LAPTOP HARDWARE REPAIR</h4><p>Broken screens, failed drives, worn keyboards and dead power ports. We source quality parts and fit them properly, with a warranty on every job.</p></div>
      </div>
      <div class="service">
        <div class="service-icon"><svg width="24" height="24" viewBox="0 0 24 24"><path d="M12 20V5M5 11l7-7 7 7" fill="none" stroke="#fff" stroke-width="2.5"/></svg></div>
        <div><h4>UPGRADES</h4><p>Faster drives, more memory and fresh software give older machines a second life. We recommend only the upgrades that will make a real difference.</p></div>
      </div>
    </div>
    <div class="dots"><i></i><i class="on"></i><i></i></div>
  </div>
</section>

<section class="testimonials" id="testimonials">
  <div class="wrap">
    <h2 class="section-title">WHAT OUR CLIENT'S SAY</h2>
    <div class="quotes">
      <div class="quote">
        <div class="avatar" role="img" aria-label="Portrait photo of a client"></div>
        <div><p>“They fixed my office laptop the same day and explained everything clearly. Fair price and great service, I will be back.”</p><div class="who">DANIEL ROSS</div><div class="role">Office Manager</div></div>
      </div>
      <div class="quote">
        <div class="avatar" role="img" aria-label="Portrait photo of a client"></div>
        <div><p>“Our small shop network runs smoothly now. Friendly, fast and professional people who clearly know their craft.”</p><div class="who">MARTIN HALE</div><div class="role">Shop Owner</div></div>
      </div>
    </div>
  </div>
</section>

<footer class="site-footer" id="contact">
  <div class="wrap">
    <div class="footer-cols">
      <div class="footer-brand">
        <div class="brand-name">Techmend</div>
        <div class="brand-tag">Computer Services</div>
      </div>
      <div class="footer-col">
        <h5>WELCOME</h5>
        <ul><li>Home</li><li>About Us</li><li>Services</li><li>Testimonials</li><li>Contact Us</li></ul>
      </div>
      <div class="footer-col">
        <h5>INFORMATION</h5>
        <ul><li>Terms &amp; Conditions</li><li>Privacy Policy</li><li>Disclaimer</li></ul>
      </div>
      <div class="footer-col">
        <h5>CONTACT INFO</h5>
        <ul><li>214 Harbor Lane, Suite 5</li><li>Springfield, ST 00000</li><li>1 (555) 014 2290</li><li>hello@techmend.example</li></ul>
      </div>
      <div class="footer-col social">
        <h5>FOLLOW US</h5>
        <ul><li><span class="social-dot"></span>Community</li><li><span class="social-dot"></span>Updates</li><li><span class="social-dot"></span>Network</li></ul>
      </div>
    </div>
  </div>
</footer>
<div class="footer-bottom">© 2024 Techmend. All rights reserved.</div>

</body>
</html>
```